Copper Kettle Fitness Flyer

We need a Flyer designed for a Revolutionary Fresh New Functional Fitness facility in Manly Sydney, Australia. We have just recently opened and now need to get the word out. Using the flyers to hand out at events also for shop counters and letterbox drops.

Our company name is Copper Kettle Fitness "Where STRENGTH Is Your FORTUNE".
We promote health and fitness to all fitness levels concentrating on functional fitness. To learn more about us and our colour scheme see attached file and also check us out on www.brightwavesocial.example/copperkettlefitnessaus

A5 Size please

Target Market(s)

The beauty of our system is it is for everyone we have girls and guys in there teens, 20's 30's 40's and 50's. Not only that we have professional athletes, military and high fitness levels all the way to people who are overweight and need to loose weight and tone up. The system caters for everyone.

Industry/Entity Type

Fitness

Requirements
Must have
• FRONT:

Free 30min Fat Blasting Experience With Your Very Own Personal Trainer !!!

New Class Starts Every 3 minutes.
30 minute Workout With A Trainer.
No Machines No Mirrors And No Attitudes.
Catering For All Fitness Levels.
Results Guaranteed Or Your Money Back.
Fun, Fresh, Clean, Revolutionary New Facility.

Back:

You Are Just Moments Away From Burning Fat Faster Than Ever Before And Getting That Body You Always Wanted !!!

Come In Today To Claim Your FREE Workout.

Ph (02) 9418 7260
Address 5/217 Harlow St North Manly 2100
www.brightwavesocial.example/copperkettlefitnessaus
Nice to have
• FRONT:

Back:

Ph (02) 9418 7260

```html
<!DOCTYPE html>
<html lang="en">
<head>
<meta charset="utf-8">
<title>Copper Kettle Fitness Flyer</title>
<link rel="stylesheet" href="https://fonts.googleapis.com/css2?family=Roboto+Condensed:ital,wght@0,400;0,700;1,400;1,700&display=swap">
<style>
  :root {
    --backdrop: #4a4849;
    --paper: #ffffff;
    --lime: #a6c83a;
    --olive: #5a7a34;
    --charcoal: #262626;
    --sky: #2f8fd0;
    --amber: #e8932a;
    --sun: #f5ea14;
    --leaf: #b9d545;
    --tick: #29a9e0;
    --ink: #3a3a3a;
  }
  html, body {
    margin: 0;
    width: 864px;
    height: 1200px;
    overflow: hidden;
    background: var(--backdrop);
  }
  .flyer {
    display: block;
    width: 864px;
    height: 1200px;
    font-family: "Roboto Condensed", "Arial Narrow", sans-serif;
  }
  .sheet { fill: var(--paper); }
  .corner-lime { fill: var(--lime); }
  .corner-olive { fill: var(--olive); }
  .dark-panel { fill: var(--charcoal); }
  .frame { fill: var(--paper); }
  .offer-diamond { fill: var(--sky); }
  .promise-diamond { fill: var(--amber); }
  .brand-square { fill: var(--amber); }
  .brand-name { fill: var(--ink); font-weight: 700; font-size: 26px; letter-spacing: 1px; }
  .offer-text { font-weight: 700; text-anchor: middle; }
  .offer-big { font-size: 46px; }
  .offer-small { font-size: 25px; }
  .fill-white { fill: var(--paper); }
  .fill-sun { fill: var(--sun); }
  .promise-text { fill: var(--paper); font-weight: 700; font-size: 26px; text-anchor: middle; }
  .feature-text { fill: var(--leaf); font-style: italic; font-size: 19px; }
  .tick-dot { fill: var(--tick); }
  .tick-mark { fill: none; stroke: var(--paper); stroke-width: 2.4; stroke-linecap: round; stroke-linejoin: round; }
  .cta-text { fill: var(--paper); font-weight: 700; font-size: 30px; }
  .cta-big { font-size: 36px; }
  .phone-icon-ring { fill: none; stroke: var(--sun); stroke-width: 2.5; }
  .phone-icon-handset { fill: var(--sun); }
  .phone-number { fill: var(--paper); font-weight: 700; font-size: 40px; }
</style>
</head>
<body>
<svg class="flyer" viewBox="0 0 864 1200" xmlns="http://www.w3.org/2000/svg">
  <defs>
    <linearGradient id="tone-cardio" x1="0" y1="0" x2="1" y2="1">
      <stop offset="0" stop-color="#8a7d74"/>
      <stop offset="0.5" stop-color="#c9a58c"/>
      <stop offset="1" stop-color="#4d5560"/>
    </linearGradient>
    <linearGradient id="tone-ball" x1="0" y1="0" x2="1" y2="1">
      <stop offset="0" stop-color="#9aa3a8"/>
      <stop offset="0.55" stop-color="#d9b9a2"/>
      <stop offset="1" stop-color="#c8352c"/>
    </linearGradient>
    <linearGradient id="tone-lift" x1="0" y1="0" x2="1" y2="1">
      <stop offset="0" stop-color="#4a4644"/>
      <stop offset="0.5" stop-color="#c7836a"/>
      <stop offset="1" stop-color="#d23a2e"/>
    </linearGradient>
  </defs>

  <rect class="sheet" x="78" y="96" width="709" height="1007"/>

  <polygon class="corner-lime" points="78,96 240,96 78,258"/>

  <g class="photo photo-cardio" role="img" aria-label="Photo of a woman and a man running on treadmills in a gym">
    <polygon points="98,240 242,96 455,96 520,262 352,430" fill="url(#tone-cardio)"/>
  </g>
  <g class="photo photo-ball" role="img" aria-label="Photo of women doing sit-ups on exercise balls">
    <polygon points="78,288 272,482 78,690" fill="url(#tone-ball)"/>
  </g>
  <g class="photo photo-lift" role="img" aria-label="Photo of a man in a red tank top lifting a barbell">
    <polygon points="335,478 528,285 738,495 545,690" fill="url(#tone-lift)"/>
  </g>

  <polygon class="dark-panel" points="787,455 787,1103 466,1103 282,918"/>
  <polygon class="corner-olive" points="78,700 466,1103 78,1103"/>

  <g class="brand">
    <rect class="brand-square" x="498" y="140" width="62" height="62"/>
    <text class="brand-name" x="574" y="165">COPPER KETTLE</text>
    <text class="brand-name" x="574" y="196">FITNESS</text>
  </g>

  <g class="offer">
    <polygon class="frame" points="300,496 520,716 300,936 80,716"/>
    <polygon class="offer-diamond" points="300,512 504,716 300,920 96,716"/>
    <g transform="rotate(-45 300 716)">
      <text class="offer-text offer-big fill-sun" x="300" y="650">FREE 30MIN</text>
      <text class="offer-text offer-big fill-white" x="300" y="698">FAT BLASTING</text>
      <text class="offer-text offer-big fill-white" x="300" y="746">EXPERIENCE</text>
      <text class="offer-text offer-small fill-white" x="300" y="790">WITH YOUR VERY OWN</text>
      <text class="offer-text offer-small fill-sun" x="300" y="820">PERSONAL TRAINER !!!</text>
    </g>
  </g>

  <g class="promise">
    <polygon class="frame" points="660,515 800,655 660,795 520,655"/>
    <polygon class="promise-diamond" points="660,530 785,655 660,780 535,655"/>
    <text class="promise-text" x="662" y="613">RESULTS</text>
    <text class="promise-text" x="662" y="647">GUARANTEED OR</text>
    <text class="promise-text" x="662" y="681">YOUR MONEY</text>
    <text class="promise-text" x="662" y="715">BACK.</text>
  </g>

  <g class="features">
    <g transform="translate(455 842)">
      <circle class="tick-dot" r="7.5"/><polyline class="tick-mark" points="-3.5,0 -1,2.8 3.8,-2.8"/>
    </g>
    <text class="feature-text" x="471" y="848">New Class Starts Every 3 minutes.</text>
    <g transform="translate(425 877)">
      <circle class="tick-dot" r="7.5"/><polyline class="tick-mark" points="-3.5,0 -1,2.8 3.8,-2.8"/>
    </g>
    <text class="feature-text" x="443" y="883">30 minute Workout With A Trainer.</text>
    <g transform="translate(393 912)">
      <circle class="tick-dot" r="7.5"/><polyline class="tick-mark" points="-3.5,0 -1,2.8 3.8,-2.8"/>
    </g>
    <text class="feature-text" x="409" y="918">No Machines No Mirrors And No Attitudes.</text>
    <g transform="translate(357 947)">
      <circle class="tick-dot" r="7.5"/><polyline class="tick-mark" points="-3.5,0 -1,2.8 3.8,-2.8"/>
    </g>
    <text class="feature-text" x="373" y="953">Fun, Fresh, Clean, Revolutionary New Facility.</text>
    <g transform="translate(396 983)">
      <circle class="tick-dot" r="7.5"/><polyline class="tick-mark" points="-3.5,0 -1,2.8 3.8,-2.8"/>
    </g>
    <text class="feature-text" x="418" y="989">Catering For All Fitness Levels.</text>
  </g>

  <g class="call-to-action">
    <text class="cta-text" x="100" y="998">COME IN TODAY</text>
    <text class="cta-text" x="100" y="1034">TO CLAIM YOUR</text>
    <text class="cta-text cta-big" x="100" y="1074"><tspan class="fill-sun">FREE</tspan> WORKOUT.</text>
  </g>

  <g class="contact-phone">
    <circle class="phone-icon-ring" cx="472" cy="1053" r="14"/>
    <path class="phone-icon-handset" d="M466,1045 q-2,8 5,15 q5,5 9,4 l1,-3 l-4,-3 l-2,2 q-4,-2 -6,-7 l2,-2 l-2,-5 z"/>
    <text class="phone-number" x="497" y="1068">(02) 9418 7260</text>
  </g>
</svg>
</body>
</html>
```